Business Card Design - Photographer

I am a landscape photographer and I require a business card design. 

I require two designs:
1)  a double sided business card
 and
b)  a single sided business card 

The single sided design can either be the same as the double sided (with just one side having all the information)....or it can be an entire new design. Its up to you.

My corporate colours are (CMYK):

Blue   69, 32, 0, 0
Grey  72,  64,  47,  31
Green  32,  2,  91,  0
Yellow   0, 19, 92, 0
Orange  0, 39, 75, 0

Colour space in final file should be in CMYK.

The details that need to be included on the card:

- Use the provided Logo
- Name: Wiktor Baranowski
- Email:   sales@vistalumeworks.com.au
- Website:    vistalumeworks.com.au
- Twitter:    twitter.com/vistalumeworks
- Facebook:   facebook.com/vistalumeworks
- Mobile  0417 539 662

Please use the attached template to design the logo to the specified size, including the marked bleed lines. I have also attached my logo in PNG (transparent background) and ai format for you to use.

The final file should be:
- Photoshop version with layers so I can edit the name/text etc. All non vector files should be high resolution at 1039 x 697 pixels at 300 dpi.

I also require a file as:
- Vector based PDF

Anyway questions please contact me.

Thank you

Industry/Entity Type

Landscape

Logo styles of interest
Pictorial/Combination Logo
Abstract Logo
Wordmark Logo
Lettermark Logo
Requirements
Must have
• The details that need to be included on the card:

- Use the provided Logo
- Name: Wiktor Baranowski
- Email: sales@vistalumeworks.com.au
- Website: vistalumeworks.com.au
- Twitter: twitter.com/vistalumeworks
- Facebook: facebook.com/vistalumeworks
- Mobile 0417 539 662

```html
<!DOCTYPE html>
<html lang="en">
<head>
<meta charset="utf-8">
<title>Vistalume Works – Business Cards</title>
<link rel="stylesheet" href="https://fonts.googleapis.com/css2?family=Cinzel:wght@700&family=Tinos&family=Open+Sans:wght@400&display=swap">
<style>
  :root {
    --brand-blue: #3d8bcb;
    --brand-grey: #3a3f55;
    --card-white: #ffffff;
    --page-bg: #eeeeee;
    --text-dark: #3a3a3a;
    --rule-grey: #b5b5b5;
  }
  * { box-sizing: border-box; margin: 0; padding: 0; }
  html, body { width: 1200px; height: 1054px; overflow: hidden; }
  body { background: var(--page-bg); position: relative; }

  .card { position: absolute; width: 766px; height: 436px; overflow: hidden; box-shadow: 0 2px 6px rgba(0,0,0,.2); }
  .card--front { left: 80px; top: 64px; background: var(--card-white); }
  .card--back { left: 350px; top: 547px; background: var(--brand-blue); }

  .front-band { position: absolute; left: 0; top: 0; width: 100%; height: 108px; background: var(--brand-blue); }
  .front-rule { position: absolute; left: 0; top: 112px; width: 100%; height: 3px; background: var(--brand-grey); }
  .front-badge { position: absolute; left: 302px; top: 26px; width: 160px; height: 160px; border-radius: 50%; background: var(--card-white); }

  .brand-name {
    position: absolute; left: 0; width: 100%; text-align: center;
    font-family: "Cinzel", serif; font-weight: 700; font-size: 34px;
    color: var(--brand-grey); letter-spacing: 0.5px; line-height: 1;
  }
  .brand-rule { position: absolute; height: 2px; background: var(--brand-grey); }

  .card--front .brand-name { top: 184px; left: -1px; }
  .card--front .brand-rule { left: 201px; width: 334px; top: 224px; }

  .address {
    position: absolute; right: 457px; top: 314px; text-align: right;
    font-family: "Tinos", serif; font-size: 19px; line-height: 28px; color: var(--text-dark);
  }
  .contact-divider { position: absolute; left: 340px; top: 274px; width: 1px; height: 136px; background: var(--rule-grey); }
  .contact-list { position: absolute; left: 367px; top: 273px; list-style: none; }
  .contact-list li {
    display: flex; align-items: center; gap: 6px; height: 28px;
    font-family: "Tinos", serif; font-size: 19px; color: var(--text-dark);
  }
  .contact-icon { width: 13px; height: 13px; flex: none; }

  .back-badge { position: absolute; left: 310px; top: 73px; width: 146px; height: 146px; border-radius: 50%; background: var(--brand-grey); }
  .card--back .brand-name { top: 236px; }
  .card--back .brand-rule { left: 190px; width: 386px; top: 277px; }
  .back-website {
    position: absolute; left: 0; width: 100%; top: 350px; text-align: center;
    font-family: "Open Sans", sans-serif; font-size: 19px; letter-spacing: 3px; color: var(--card-white);
  }
</style>
</head>
<body>

<section class="card card--front" aria-label="Business card front">
  <div class="front-band"></div>
  <div class="front-rule"></div>
  <div class="front-badge"></div>
  <h1 class="brand-name">VISTALUME WORKS</h1>
  <div class="brand-rule"></div>

  <address class="address">00, Complex Name<br>State Name, City 0020</address>
  <div class="contact-divider"></div>
  <ul class="contact-list">
    <li>
      <svg class="contact-icon" viewBox="0 0 13 13" aria-hidden="true"><rect x="3" y="0.5" width="7" height="12" rx="1.5" fill="#555"/><rect x="4.3" y="2" width="4.4" height="7" fill="#fff"/></svg>
      0417 539 662
    </li>
    <li>
      <svg class="contact-icon" viewBox="0 0 13 13" aria-hidden="true"><rect width="13" height="13" rx="2" fill="#5aaee0"/></svg>
      vistalumeworks
    </li>
    <li>
      <svg class="contact-icon" viewBox="0 0 13 13" aria-hidden="true"><rect width="13" height="13" rx="2" fill="#4a67a8"/></svg>
      vistalumeworks
    </li>
    <li>
      <svg class="contact-icon" viewBox="0 0 13 13" aria-hidden="true"><rect x="0.5" y="3" width="12" height="8" fill="#555"/><path d="M0.5 3 L6.5 7.5 L12.5 3" stroke="#fff" stroke-width="1" fill="none"/></svg>
      sales@vistalumeworks.com.au
    </li>
    <li>
      <svg class="contact-icon" viewBox="0 0 13 13" aria-hidden="true"><circle cx="6.5" cy="6.5" r="5.5" fill="#555"/><path d="M1 6.5 H12 M6.5 1 V12" stroke="#fff" stroke-width="0.8"/></svg>
      www.vistalumeworks.com.au
    </li>
  </ul>
</section>

<section class="card card--back" aria-label="Business card back">
  <div class="back-badge"></div>
  <h2 class="brand-name">VISTALUME WORKS</h2>
  <div class="brand-rule"></div>
  <p class="back-website">www.vistalumeworks.com.au</p>
</section>

</body>
</html>
```